Business Card Re-Design/Update

We'd like to update out business cards. I've included our current "Style guide" which has the colour scheme of the organisation in it. I've also included the branding files with logos etc in them.

I've also included a copy of one of our existing cards so that you can see how ugly/dated they look. I'd like a fresh modern corporate look.

Target Market(s)

These are for our clients, potential clients, industry contacts - like all business cards

Contact Information for Business Card

Name
Position
Company Address - Level 1, 47 Fernby Street, Carlow Qld 4072
Direct Phone
mobile
Email
Website -www.korvalit.com.au
Logo

Colors

Designer to choose colors to be used in the design.

Requirements
Must have
• Main Logo
• Cards will need to be editable to be able to personalize them for each new employee.
Nice to have
• The MapOut, ShipWell, KeepSteady would be okay to have if they can be sensibly and professionally added to the look without detracting from the main imagery.
• Maybe they could go on the back of the card? will leave this to your creative discretion as to whether/where they fit.
Should not have
• Should not have decorative or script fonts

```html
<!DOCTYPE html>
<html lang="en">
<head>
<meta charset="utf-8">
<title>korvalIT business card</title>
<link href="https://fonts.googleapis.com/css2?family=Open+Sans:wght@400;600;700&display=swap" rel="stylesheet">
<style>
  :root {
    --brand-red: #d71920;
    --ink: #3a3a3c;
    --ink-soft: #4a4a4c;
    --paper: #ffffff;
    --backdrop: #f1f1f1;
    --rule: #d9d9d9;
  }
  * { margin: 0; padding: 0; box-sizing: border-box; }
  html, body { width: 1200px; height: 881px; overflow: hidden; }
  body {
    background: var(--backdrop);
    font-family: "Open Sans", Arial, sans-serif;
    position: relative;
  }
  .card {
    position: absolute;
    top: 290px;
    width: 540px;
    height: 300px;
    box-shadow: 0 6px 18px rgba(0,0,0,0.12);
  }
  .card-front { left: 40px; background: var(--paper); }
  .card-back { left: 620px; background: var(--brand-red); }

  .wordmark {
    display: flex;
    align-items: center;
    gap: 12px;
    font-weight: 600;
    letter-spacing: -0.5px;
  }
  .wordmark-mark { display: block; }

  .card-front .wordmark {
    position: absolute;
    left: 32px;
    top: 34px;
    font-size: 38px;
    color: var(--ink);
  }
  .card-front .wordmark-mark {
    width: 30px; height: 30px;
    background: var(--brand-red);
  }

  .contact-block {
    position: absolute;
    left: 92px;
    top: 112px;
    color: var(--ink-soft);
  }
  .person-name {
    font-size: 20px;
    font-weight: 700;
    color: var(--brand-red);
    line-height: 1.15;
  }
  .person-title { font-size: 12.5px; line-height: 1.4; }
  .divider {
    width: 34px; height: 1px;
    background: var(--rule);
    margin: 8px 0 10px;
  }
  .address { font-size: 12.5px; margin-bottom: 10px; }
  .contact-list { list-style: none; }
  .contact-list li {
    display: flex;
    align-items: center;
    gap: 9px;
    font-size: 12.5px;
    line-height: 17.5px;
  }
  .contact-icon { width: 11px; height: 11px; flex: none; fill: var(--brand-red); }

  .card-back .wordmark {
    position: absolute;
    left: 0; right: 0;
    top: 88px;
    flex-direction: column;
    gap: 14px;
    font-size: 48px;
    color: var(--paper);
  }
  .card-back .wordmark-mark {
    width: 44px; height: 44px;
    background: var(--paper);
  }
  .service-list {
    position: absolute;
    left: 0; right: 0;
    top: 244px;
    display: flex;
    justify-content: center;
    gap: 30px;
    list-style: none;
    color: var(--paper);
    font-size: 14px;
    font-weight: 600;
  }
  .service-list li { display: flex; align-items: center; gap: 6px; }
  .service-bullet { width: 8px; height: 8px; border: 1.5px solid var(--paper); }
</style>
</head>
<body>

<section class="card card-front" aria-label="Business card front">
  <div class="wordmark">
    <span class="wordmark-mark"></span>
    <span class="wordmark-name">korvalIT</span>
  </div>

  <div class="contact-block">
    <p class="person-name">Mira Castell</p>
    <p class="person-title">Business Development Manager</p>
    <div class="divider"></div>
    <p class="address">Level 1, 47 Fernby Street, Carlow Qld 4072</p>
    <ul class="contact-list">
      <li>
        <svg class="contact-icon" viewBox="0 0 12 12"><path d="M3 0h6a1 1 0 0 1 1 1v10a1 1 0 0 1-1 1H3a1 1 0 0 1-1-1V1a1 1 0 0 1 1-1zm0 1.5v7.5h6V1.5z"/></svg>
        +61 (0)400 555 218
      </li>
      <li>
        <svg class="contact-icon" viewBox="0 0 12 12"><path d="M2.4 0.6l2 2.2-1 1.4c.8 1.7 2 2.9 3.6 3.6l1.4-1 2.2 2-1.2 1.8C4.8 10.4 1.4 7 .6 1.8z"/></svg>
        +61 (0)7 5550 1246
      </li>
      <li>
        <svg class="contact-icon" viewBox="0 0 12 12"><path d="M0 2h12v8H0zm1 1l5 3.5L11 3z"/></svg>
        mcastell@korvalit.com.au
      </li>
      <li>
        <svg class="contact-icon" viewBox="0 0 12 12"><path d="M6 0a6 6 0 1 0 0 12A6 6 0 0 0 6 0zm0 1.2c.7.8 1.2 2.2 1.3 3.8H4.7C4.8 3.4 5.3 2 6 1.2zM1.3 5h2.4c.1-1.5.5-2.8 1-3.6A4.8 4.8 0 0 0 1.3 5zm0 2A4.8 4.8 0 0 0 4.7 10.6c-.5-.8-.9-2.1-1-3.6zm3.4 0h2.6c-.1 1.6-.6 3-1.3 3.8C5.3 10 4.8 8.6 4.7 7zm3.6 0c-.1 1.5-.5 2.8-1 3.6A4.8 4.8 0 0 0 10.7 7zm2.4-2A4.8 4.8 0 0 0 7.3 1.4c.5.8.9 2.1 1 3.6z"/></svg>
        www.korvalit.com.au
      </li>
    </ul>
  </div>
</section>

<section class="card card-back" aria-label="Business card back">
  <div class="wordmark">
    <span class="wordmark-mark"></span>
    <span class="wordmark-name">korvalIT</span>
  </div>
  <ul class="service-list">
    <li><span class="service-bullet"></span>MapOut</li>
    <li><span class="service-bullet"></span>KeepSteady</li>
    <li><span class="service-bullet"></span>ShipWell</li>
  </ul>
</section>

</body>
</html>
```